Business card design needed

I run a Beautician studio (for 7 years now)
I offer
- Velmo Body Sugaring
- Ruby Glaze
- Nails
- Facials
- Manicure
- Foot Treatment
It might not be necessary to list all those treatments?
Maybe the link to the Website is sufficient?
I leave that up to you ...
(more info on www.FernAndDewByLenka.com.au)
Velmo BodySugaring is our biggest success, It replaces waxing.
I would like to incorporate the logo into the Business Card.
We had many complaints regarding our old Business Cards as the Phone Number was to small.
On the backside, we would like a "your next Appointment" section.
Looking forward to you Design, cheers ... Lenka
Industry/Entity Type
Business
Contact Information for Business Card
Fern by Dew by Lenka
14 Korrin Sqr 3942 Marrowvale
www.FernAndDewByLenka.com.au
03 9481 2267

```html
<!DOCTYPE html>
<html lang="en">
<head>
<meta charset="utf-8">
<title>Fern by Dew by Lenka – Business Cards</title>
<link rel="stylesheet" href="https://fonts.googleapis.com/css2?family=Cinzel:wght@400;600&family=Libre+Baskerville:wght@400;700&family=Open+Sans:wght@400;600;700&display=swap">
<style>
  :root {
    --backdrop: #1c1c1c;
    --card: #ffffff;
    --band-start: #e8542a;
    --band-end: #f6c821;
    --green: #1d9a4a;
    --ink: #333333;
    --ink-soft: #555555;
    --sun: #f19a1f;
    --rule: #888888;
    --watermark: #f3f3ee;
  }
  * { box-sizing: border-box; margin: 0; padding: 0; }
  html, body { width: 1200px; height: 728px; overflow: hidden; }
  body {
    background: var(--backdrop);
    font-family: "Open Sans", Arial, sans-serif;
    color: var(--ink);
    position: relative;
  }
  .card {
    position: absolute;
    width: 540px;
    height: 308px;
    background: var(--card);
    overflow: hidden;
  }
  .card--front { left: 41px; top: 37px; }
  .card--appointment-branded { left: 616px; top: 37px; }
  .card--hours { left: 44px; top: 380px; }
  .card--appointment-plain { left: 624px; top: 384px; }

  /* Front card bands */
  .band {
    position: absolute;
    left: 0; width: 100%;
    background: linear-gradient(90deg, var(--band-start), #ef8a25 50%, var(--band-end));
    color: #fff;
    text-align: center;
  }
  .band--top {
    top: 0; height: 35px;
    font-family: "Libre Baskerville", Georgia, serif;
    font-weight: 700;
    font-size: 20px;
    letter-spacing: 3px;
    line-height: 35px;
  }
  .band--bottom {
    bottom: 0; height: 36px;
    font-family: "Libre Baskerville", Georgia, serif;
    font-size: 13px;
    letter-spacing: 3.5px;
    line-height: 36px;
  }
  .stripe {
    position: absolute; left: 0; width: 100%; height: 4px;
    background: var(--green);
  }
  .stripe--top { top: 38px; }
  .stripe--bottom { bottom: 39px; }

  /* Brand name stand-in */
  .brand {
    position: absolute;
    left: 0; width: 100%;
    text-align: center;
  }
  .brand__dot {
    display: block;
    margin: 0 auto;
    border-radius: 50%;
    background: var(--sun);
  }
  .brand__name {
    display: block;
    font-family: "Cinzel", Georgia, serif;
    font-weight: 600;
    color: var(--ink);
    white-space: nowrap;
  }
  .card--front .brand { top: 72px; }
  .card--front .brand__dot { width: 64px; height: 64px; }
  .card--front .brand__name { font-size: 25px; margin-top: 16px; letter-spacing: 1px; }

  .card--hours .brand { top: 42px; }
  .card--hours .brand__dot { width: 76px; height: 76px; }
  .card--hours .brand__name { font-size: 28px; margin-top: 18px; letter-spacing: 1px; }

  .card--appointment-branded .brand {
    left: auto; right: 28px; top: 18px; width: 140px;
  }
  .card--appointment-branded .brand__dot { width: 40px; height: 40px; }
  .card--appointment-branded .brand__name { font-size: 11px; margin-top: 8px; }

  .watermark {
    position: absolute;
    left: 0; top: 215px; width: 100%;
    text-align: center;
    font-family: "Cinzel", Georgia, serif;
    font-weight: 600;
    font-size: 30px;
    color: var(--watermark);
    letter-spacing: 1px;
    white-space: nowrap;
  }

  /* Contact row */
  .contact {
    position: absolute;
    top: 230px; left: 0; width: 100%;
    display: flex; justify-content: center; align-items: center;
    gap: 8px;
    font-size: 14px;
    color: var(--ink);
  }
  .contact__phone { font-size: 15px; margin-right: 10px; }
  .contact svg { width: 15px; height: 15px; }

  /* Hours card */
  .hours__url {
    position: absolute; top: 202px; width: 100%; text-align: center;
    font-size: 14px; letter-spacing: 2.4px; color: var(--ink);
  }
  .hours__title {
    position: absolute; top: 234px; width: 100%; text-align: center;
    font-size: 19px; font-weight: 700; letter-spacing: 1.5px; color: var(--ink-soft);
  }
  .hours__times {
    position: absolute; top: 268px; width: 100%; text-align: center;
    font-size: 15px; font-weight: 600; color: var(--ink-soft);
  }
  .hours__sep { color: #aaa; margin: 0 6px; }

  /* Appointment cards */
  .appt__title {
    position: absolute; top: 52px; left: 35px;
    font-family: "Cinzel", Georgia, serif; font-weight: 600;
    font-size: 17px; color: var(--green); letter-spacing: 0.5px;
  }
  .appt__row {
    position: absolute; left: 35px;
    display: flex; align-items: flex-end;
    font-size: 14px; color: var(--ink);
  }
  .appt__row--name { top: 90px; }
  .appt__row--date { top: 127px; }
  .appt__row--next { top: 164px; }
  .appt__row--days { top: 200px; font-weight: 600; color: var(--ink-soft); }
  .fill-line { display: inline-block; border-bottom: 1px dotted var(--rule); height: 12px; margin-left: 8px; }
  .fill-line--solid { border-bottom: 1px solid var(--rule); }
  .fill-box {
    display: inline-block; width: 96px; height: 20px;
    border: 1px solid #777; margin-left: 10px;
  }
  .day-box {
    display: inline-block; width: 34px; height: 20px;
    border: 1px solid #777; margin: 0 12px 0 10px;
  }
  .appt__note {
    position: absolute; left: 32px; top: 250px; width: 480px;
    font-size: 12.5px; line-height: 18px; color: var(--ink);
  }
</style>
</head>
<body>

<section class="card card--front" aria-label="Business card front">
  <div class="band band--top">Fern by Dew by Lenka</div>
  <div class="stripe stripe--top"></div>
  <div class="brand">
    <span class="brand__dot"></span>
    <span class="brand__name">Velmo Body Sugaring</span>
  </div>
  <div class="contact">
    <svg viewBox="0 0 16 16" aria-hidden="true"><circle cx="8" cy="8" r="7" fill="none" stroke="#f19a1f" stroke-width="1.6"/><path d="M5.5 4.5l1.6-.3.8 2-1 .8a5 5 0 0 0 2.1 2.1l.8-1 2 .8-.3 1.6c-3 .4-6.4-3-6-6z" fill="#f19a1f"/></svg>
    <span class="contact__phone">03 9481 2267</span>
    <svg viewBox="0 0 16 16" aria-hidden="true"><circle cx="8" cy="8" r="7" fill="#f19a1f"/><ellipse cx="8" cy="8" rx="3" ry="7" fill="none" stroke="#fff" stroke-width="1"/><line x1="1" y1="8" x2="15" y2="8" stroke="#fff" stroke-width="1"/></svg>
    <span class="contact__url">www.FernAndDewByLenka.com.au</span>
  </div>
  <div class="stripe stripe--bottom"></div>
  <div class="band band--bottom">14 Korrin Sqr 3942 Marrowvale</div>
</section>

<section class="card card--appointment-branded" aria-label="Appointment card">
  <div class="brand">
    <span class="brand__dot"></span>
    <span class="brand__name">Velmo Body Sugaring</span>
  </div>
  <h2 class="appt__title">YOUR APPOINTMENT</h2>
  <div class="appt__row appt__row--name">Name :<span class="fill-line" style="width:270px"></span></div>
  <div class="appt__row appt__row--date">Date :<span class="fill-line fill-line--solid" style="width:96px;margin-left:18px"></span>&nbsp;&nbsp;Time :<span class="fill-line fill-line--solid" style="width:92px"></span>&nbsp;am / pm</div>
  <div class="appt__row appt__row--next">Next Appointment<span class="fill-box"></span><span class="fill-box" style="margin-left:26px"></span></div>
  <div class="appt__row appt__row--days">MON<span class="day-box"></span>TUE<span class="day-box"></span>WED<span class="day-box"></span>THU<span class="day-box"></span>FRI<span class="day-box"></span>SAT<span class="day-box"></span></div>
  <p class="appt__note">It would be appreciated if 24 hours notice could be given if you are unable to attend an appointment</p>
</section>

<section class="card card--hours" aria-label="Business card back with hours">
  <div class="brand">
    <span class="brand__dot"></span>
    <span class="brand__name">Velmo Body Sugaring</span>
  </div>
  <div class="hours__url">www.FernAndDewByLenka.com.au</div>
  <h2 class="hours__title">Hours of Operation</h2>
  <div class="hours__times">Mon - Fri: 8.00am - 6.30pm<span class="hours__sep">|</span>Saturday: 8.00am - 1.00pm</div>
</section>

<section class="card card--appointment-plain" aria-label="Appointment card">
  <div class="watermark" aria-hidden="true">Velmo Body Sugaring</div>
  <h2 class="appt__title">YOUR APPOINTMENT</h2>
  <div class="appt__row appt__row--name">Name :<span class="fill-line" style="width:290px"></span></div>
  <div class="appt__row appt__row--date">Date :<span class="fill-line fill-line--solid" style="width:96px;margin-left:18px"></span>&nbsp;&nbsp;Time :<span class="fill-line fill-line--solid" style="width:92px"></span>&nbsp;am / pm</div>
  <div class="appt__row appt__row--next">Next Appointment<span class="fill-box"></span><span class="fill-box" style="margin-left:26px"></span></div>
  <div class="appt__row appt__row--days">MON<span class="day-box"></span>TUE<span class="day-box"></span>WED<span class="day-box"></span>THU<span class="day-box"></span>FRI<span class="day-box"></span>SAT<span class="day-box"></span></div>
  <p class="appt__note">It would be appreciated if 24 hours notice could be given if you are unable to attend an appointment</p>
</section>

</body>
</html>
```